Property Finance Company - Orbin Funding Limited

Background: Orbin Funding Group Limited is a private property finance company. Orbin Funding Group has capital to directly fund first mortgage, mezzanine and preferred equity financing. We also acquire performing, sub-performing and distressed debt.

Orbin Fundings management philosophy emphasises expertise, innovation, wisdom, honesty and competitiveness. Orbin Funding are not finance brokers - we provide debt funding to the commercial property and residential development sectors. Our process is built from experience and cumutavely Orbin Fundings Directors have in excess of 60 years wisdom.

The aim of the website will be to increase brand awareness, provide clients with comfort around our level of skill and background on who we are, generate more sales, and provide examples of projects that we have funded.

The website is a new product launch, and we need to use our Orbin Funding logo that has just been designed. We like a dark background, and either black/silver/grey/ jade green, or black/gold/jade green colours.

Our unique advantages are that we have fast turnaround times, we can solve clients funding problems and we know what we are doing. Our target audience will be viewing the website on both desktop and mobile devices.

We would like to have the following pages:

Home
About
Team
Services
Project Experience
Contact

Competitors Website: http://www.tarvolo.example/

We would also like to have the option of video footage in our website, as you can see in our competitors website.

Overall we want a really slick, elegant but modern website that is better than www.tarvolo.example

Target Market(s)

Finance borrowers, property developers, accountants, lawyers, businesspeople, high net worth people

Industry/Entity Type

Finance

Requirements
Must have
• Please see project description
Nice to have
Should not have

```html
<!DOCTYPE html>
<html lang="en">
<head>
<meta charset="utf-8">
<title>Orbin Funding Group</title>
<link rel="stylesheet" href="https://fonts.googleapis.com/css2?family=EB+Garamond:wght@400;500;600&family=Roboto:ital,wght@0,400;0,500;1,400&display=swap">
<style>
:root{
  --teal:#3aaba2;
  --teal-dark:#2f968e;
  --ink:#222222;
  --text:#555555;
  --muted:#777777;
  --dark:#333333;
  --darker:#2a2a2a;
  --grey-band:#e8e8e8;
  --white:#ffffff;
}
*{box-sizing:border-box;margin:0;padding:0}
html,body{width:1200px;height:3297px;overflow:hidden}
body{position:relative;background:var(--white);font-family:"Roboto",Arial,sans-serif;color:var(--text)}
.abs{position:absolute}

/* header */
.site-header{left:0;top:0;width:1200px;height:136px;background:var(--white)}
.brand{left:77px;top:38px;display:flex;align-items:center;gap:12px}
.brand-mark{width:26px;height:26px;border-radius:50%;background:var(--muted)}
.brand-name{font-family:"EB Garamond",Georgia,serif;font-size:21px;font-weight:500;color:#555;letter-spacing:1px;line-height:1.15;width:150px}
.main-nav{top:0;left:0;width:1200px;height:136px}
.main-nav a{position:absolute;top:62px;font-size:17px;color:#555;text-decoration:none}
.main-nav a.active{color:var(--teal)}
.nav-underline{left:503px;top:130px;width:80px;height:4px;background:var(--teal)}

/* hero */
.hero{left:0;top:136px;width:1200px;height:583px;
  background:
    linear-gradient(180deg,rgba(210,222,226,.55) 0%,rgba(150,168,172,.25) 30%,rgba(20,26,28,0) 55%,rgba(10,14,16,.55) 100%),
    linear-gradient(90deg,#1a2123 0%,#3c4a4e 18%,#56676b 36%,#7d8f92 52%,#6a7b7e 64%,#3f4d50 80%,#2a3436 100%);}
.hero-shade{left:620px;top:136px;width:580px;height:583px;background:linear-gradient(90deg,rgba(10,14,16,0),rgba(10,14,16,.35))}
.hero-title{left:664px;top:372px;font-family:"EB Garamond",Georgia,serif;font-size:37px;font-weight:500;color:var(--white);letter-spacing:.3px;white-space:nowrap}
.hero-text{left:664px;top:432px;width:420px;font-size:15px;line-height:28px;color:var(--white)}
.btn{top:508px;height:44px;display:flex;align-items:center;justify-content:center;font-family:"EB Garamond",Georgia,serif;font-size:17px;letter-spacing:1px;border-radius:3px}
.btn-outline{left:660px;width:178px;border:2px solid var(--white);color:var(--white)}
.btn-solid{left:848px;width:181px;background:var(--white);color:var(--ink)}

/* services */
.band-grey{left:0;top:719px;width:1200px;height:626px;background:var(--grey-band)}
.service-card{top:690px;width:240px;height:270px;background:var(--white);border-bottom:5px solid var(--teal);text-align:center}
.service-card .icon{height:52px;margin-top:66px;display:flex;justify-content:center;align-items:flex-end}
.service-card h3{margin-top:26px;font-family:"EB Garamond",Georgia,serif;font-size:23px;font-weight:500;color:#444}
.service-card p{margin:8px auto 0;width:210px;font-size:14px;line-height:24px;color:var(--muted)}

/* welcome */
.band-dark{left:0;top:1345px;width:1200px;height:354px;background:var(--dark)}
.video-frame{left:235px;top:1066px;width:728px;height:415px;
  background:
    linear-gradient(180deg,rgba(235,237,238,.9) 0%,rgba(220,223,225,.6) 40%,rgba(60,70,80,0) 60%),
    linear-gradient(90deg,#8d9aa5 0%,#c9ced2 25%,#e2e4e5 45%,#b8bfc5 65%,#5f7388 85%,#46607a 100%);}
.play{left:566px;top:1241px}
.welcome-title{left:0;top:1526px;width:1200px;text-align:center;font-family:"EB Garamond",Georgia,serif;font-size:32px;font-weight:500;color:var(--white);letter-spacing:.5px}
.welcome-text{left:135px;top:1574px;width:930px;text-align:center;font-size:14px;line-height:26px;color:var(--white)}

/* experts */
.section-title{left:0;width:1200px;text-align:center;font-family:"EB Garamond",Georgia,serif;font-size:32px;font-weight:500;color:var(--ink)}
.section-title span{color:var(--teal)}
.expert-photo{top:1802px;width:240px;height:260px}
.expert-name{top:2086px;width:240px;text-align:center;font-family:"EB Garamond",Georgia,serif;font-size:23px;color:#333}
.expert-role{top:2122px;width:240px;text-align:center;font-size:14px;color:var(--muted)}

/* expertise */
.band-teal{left:0;top:2200px;width:1200px;height:334px;background:var(--teal)}
.expertise-title{left:0;top:2238px;width:1200px;text-align:center;font-family:"EB Garamond",Georgia,serif;font-size:31px;color:var(--white)}
.expertise-box{top:2301px;width:240px;height:176px;border:2px solid rgba(255,255,255,.55);border-radius:6px;padding:22px 0 0 26px;color:var(--white)}
.expertise-box .num{font-size:32px;line-height:34px}
.expertise-box h4{margin-top:10px;font-family:"EB Garamond",Georgia,serif;font-size:22px;font-weight:600}
.expertise-box p{margin-top:4px;font-size:14px;line-height:24px}

/* testimonial */
.avatar{left:556px;top:2637px;width:88px;height:88px;border-radius:50%;border:4px solid var(--teal);background:radial-gradient(circle at 50% 45%,#d9c3b6 0%,#9a7c6c 45%,#3a2f2c 100%)}
.quote{left:245px;top:2741px;width:710px;text-align:center;font-size:14px;font-style:italic;line-height:28px;color:#666}
.client{left:0;top:2804px;width:1200px;text-align:center;font-size:15px;color:#555}
.arrow{top:2718px}

/* footer */
.site-footer{left:0;top:2879px;width:1200px;height:352px;background:var(--dark)}
.footer-brand{left:77px;top:3030px;display:flex;align-items:center;gap:14px}
.footer-brand .brand-mark{width:40px;height:40px;background:#777}
.footer-brand .brand-name{font-size:33px;color:#8a8a8a;width:250px}
.footer-head{top:2938px;font-family:"EB Garamond",Georgia,serif;font-size:24px;font-weight:500;color:var(--white);letter-spacing:1px}
.footer-links{left:437px;top:2990px;list-style:none}
.footer-links li{position:relative;height:33px;padding-left:25px;font-size:14px;color:var(--white);line-height:20px}
.footer-links li::before{content:"";position:absolute;left:3px;top:5px;width:10px;height:10px;border-radius:50%;background:var(--teal)}
.contact-item{left:791px;display:flex;gap:18px;font-size:14px;line-height:26px;color:var(--white)}
.contact-item svg{flex:none;margin-top:3px}
.copyright{left:0;top:3231px;width:1200px;height:66px;background:var(--darker);border-top:1px solid #444;text-align:center;line-height:64px;font-size:14px;color:var(--white)}
</style>
</head>
<body>

<header class="abs site-header">
  <div class="abs brand"><span class="brand-mark"></span><span class="brand-name">Orbin Funding Group</span></div>
  <nav class="abs main-nav">
    <a class="active" style="left:516px">Home</a>
    <a style="left:603px">About</a>
    <a style="left:687px">Team</a>
    <a style="left:768px">Services</a>
    <a style="left:874px">Project Experience</a>
    <a style="left:1057px">Contact</a>
  </nav>
  <div class="abs nav-underline"></div>
</header>

<section class="abs hero" role="img" aria-label="Business people meeting and shaking hands in a bright glass office lobby"></section>
<div class="abs hero-shade"></div>
<h1 class="abs hero-title">ORBIN FUNDING GROUP</h1>
<p class="abs hero-text">Lorem ipsum dolor sit amet, consectetur adipiscing elit. Nam tempor faucibus ante.</p>
<div class="abs btn btn-outline">READ MORE</div>
<div class="abs btn btn-solid">CONTACT US</div>

<div class="abs band-grey"></div>

<article class="abs service-card" style="left:77px">
  <div class="icon"><svg width="70" height="44" viewBox="0 0 70 44"><rect x="14" y="6" width="52" height="30" rx="4" fill="var(--teal)"/><circle cx="40" cy="21" r="9" fill="#fff"/><text x="40" y="26" font-size="13" font-family="Roboto" font-weight="700" text-anchor="middle" fill="var(--teal)">$</text><rect x="2" y="24" width="18" height="14" rx="3" fill="var(--teal-dark)"/></svg></div>
  <h3>Debt funding</h3>
  <p>Lorem ipsum dolor sit amet, consectetur adipiscing elit.</p>
</article>
<article class="abs service-card" style="left:347px">
  <div class="icon"><svg width="70" height="50" viewBox="0 0 70 50"><circle cx="38" cy="16" r="13" fill="none" stroke="var(--teal)" stroke-width="3"/><text x="38" y="22" font-size="15" font-family="Roboto" font-weight="700" text-anchor="middle" fill="var(--teal)">$</text><path d="M8 38 L26 36 L40 40 L62 34 L62 44 L40 48 L8 46 Z" fill="var(--teal)"/></svg></div>
  <h3>Mezzanine</h3>
  <p>Lorem ipsum dolor sit amet, consectetur adipiscing elit.</p>
</article>
<article class="abs service-card" style="left:615px">
  <div class="icon"><svg width="70" height="50" viewBox="0 0 70 50"><path d="M20 20 L38 4 L56 20 L52 20 L52 34 L24 34 L24 20 Z" fill="var(--teal)"/><text x="38" y="30" font-size="13" font-family="Roboto" font-weight="700" text-anchor="middle" fill="#fff">$</text><path d="M6 40 L24 38 L38 42 L62 36 L62 46 L38 50 L6 48 Z" fill="var(--teal)"/></svg></div>
  <h3>Equity financing</h3>
  <p>Lorem ipsum dolor sit amet, consectetur adipiscing elit.</p>
</article>
<article class="abs service-card" style="left:884px">
  <div class="icon"><svg width="70" height="50" viewBox="0 0 70 50"><rect x="10" y="30" width="9" height="18" fill="var(--teal)"/><rect x="24" y="24" width="9" height="24" fill="var(--teal)"/><rect x="38" y="18" width="9" height="30" fill="var(--teal)"/><rect x="52" y="10" width="9" height="38" fill="var(--teal)"/><path d="M8 24 L28 12 L42 16 L60 2" fill="none" stroke="var(--teal)" stroke-width="3"/></svg></div>
  <h3>Perdorming</h3>
  <p>Lorem ipsum dolor sit amet, consectetur adipiscing elit.</p>
</article>

<div class="abs band-dark"></div>
<div class="abs video-frame" role="img" aria-label="Video still of a presenter speaking to colleagues around a conference table"></div>
<svg class="abs play" width="66" height="66" viewBox="0 0 66 66"><circle cx="33" cy="33" r="29" fill="none" stroke="#fff" stroke-width="4"/><path d="M26 20 L47 33 L26 46 Z" fill="#fff"/></svg>
<h2 class="abs welcome-title">WELCOME TO ORBIN FUNDING GROUP</h2>
<p class="abs welcome-text">Lorem ipsum dolor sit amet, consectetur adipiscing elit. Nam tempor faucibus ante, eget vulputate libero pharetra eu. Nulla at felis eros. Sed ut metus justo. Suspendisse vestibulum dui at magna rutrum vestibulum. Vestibulum ante ipsum primis in faucibus orci luctus et ultrices posuere cubilia Curae; Nullam eget blandit augue. Sed tempus sapien purus, ac sollicitudin sem porttitor a.</p>

<h2 class="abs section-title" style="top:1736px">MEET OUR <span>EXPERTS</span></h2>
<div class="abs expert-photo" style="left:77px;background:linear-gradient(180deg,#eceeef 0%,#dfe2e4 35%,#c7d2dc 70%,#aebdca 100%)" role="img" aria-label="Portrait of the chief executive officer"></div>
<div class="abs expert-photo" style="left:347px;background:linear-gradient(180deg,#f4f4f4 0%,#ebe6e4 40%,#ddd0d6 75%,#cdbfd6 100%)" role="img" aria-label="Portrait of the chief operations officer"></div>
<div class="abs expert-photo" style="left:615px;background:linear-gradient(135deg,#f2f2f2 0%,#f2f2f2 38%,#9ad6cd 38%,#6db5aa 70%,#4f988e 100%)" role="img" aria-label="Portrait of the chief technical officer"></div>
<div class="abs expert-photo" style="left:884px;background:linear-gradient(180deg,#6e5f55 0%,#9b8273 40%,#c9a58c 75%,#d8b9a2 100%)" role="img" aria-label="Portrait of the finance team member"></div>
<div class="abs expert-name" style="left:77px">Member Name</div>
<div class="abs expert-name" style="left:347px">Member Name</div>
<div class="abs expert-name" style="left:615px">Member Name</div>
<div class="abs expert-name" style="left:884px">Member Name</div>
<div class="abs expert-role" style="left:77px">Chief Executive Officer</div>
<div class="abs expert-role" style="left:347px">Chief Operations Officer</div>
<div class="abs expert-role" style="left:615px">Chief Technical Officer</div>
<div class="abs expert-role" style="left:884px">Finance</div>

<div class="abs band-teal"></div>
<h2 class="abs expertise-title">EXPERTISE</h2>
<div class="abs expertise-box" style="left:77px"><div class="num">01</div><h4>Innovation</h4><p>Lorem ipsum dolor sit amet, consectetur adipiscing elit.</p></div>
<div class="abs expertise-box" style="left:347px"><div class="num">02</div><h4>Wisdom</h4><p>Lorem ipsum dolor sit amet, consectetur adipiscing elit.</p></div>
<div class="abs expertise-box" style="left:615px"><div class="num">03</div><h4>Honesty</h4><p>Lorem ipsum dolor sit amet, consectetur adipiscing elit.</p></div>
<div class="abs expertise-box" style="left:884px"><div class="num">04</div><h4>Competitivenes</h4><p>Lorem ipsum dolor sit amet, consectetur adipiscing elit.</p></div>

<h2 class="abs section-title" style="top:2572px">WHAT OUR <span>CLIENT SAY</span></h2>
<div class="abs avatar" role="img" aria-label="Client portrait"></div>
<p class="abs quote">It is a long established fact that a reader will be distracted by the readable content of a page when looking at its layout. The point of using Lorem Ipsum is that it has a more-or-less normal distribution of letters..</p>
<div class="abs client">- Client Name</div>
<svg class="abs arrow" style="left:52px" width="20" height="28" viewBox="0 0 20 28"><path d="M15 3 L5 14 L15 25" fill="none" stroke="var(--teal)" stroke-width="3"/></svg>
<svg class="abs arrow" style="left:1120px" width="20" height="28" viewBox="0 0 20 28"><path d="M5 3 L15 14 L5 25" fill="none" stroke="var(--teal)" stroke-width="3"/></svg>

<footer class="abs site-footer"></footer>
<div class="abs footer-brand"><span class="brand-mark"></span><span class="brand-name">Orbin Funding Group</span></div>
<h3 class="abs footer-head" style="left:437px">USEFUL LINKS</h3>
<ul class="abs footer-links">
  <li>Home</li><li>About</li><li>Team</li><li>Services</li><li>Project Experience</li><li>Contact</li>
</ul>
<h3 class="abs footer-head" style="left:791px">CONTACT INFO</h3>
<div class="abs contact-item" style="top:2988px">
  <svg width="16" height="22" viewBox="0 0 16 22"><path d="M8 1 C3.6 1 1 4.2 1 8 C1 13 8 21 8 21 C8 21 15 13 15 8 C15 4.2 12.4 1 8 1 Z" fill="var(--teal)"/><circle cx="8" cy="8" r="3" fill="var(--dark)"/></svg>
  <span>Lorem Ipsum is simply dummy<br>text of the printing.</span>
</div>
<div class="abs contact-item" style="top:3053px">
  <svg width="16" height="18" viewBox="0 0 16 18"><path d="M3 1 L6 1 L7.5 5 L5.5 6.5 C6.5 9 8 10.5 10 11.5 L11.5 9.5 L15 11 L15 14 C15 15.5 13.5 17 12 16.5 C6 15 1.5 10 1 4 C1 2.5 2 1 3 1 Z" fill="var(--teal)"/></svg>
  <span>123 456 7890</span>
</div>
<div class="abs contact-item" style="top:3095px">
  <svg width="18" height="16" viewBox="0 0 18 16"><rect x="1" y="2" width="16" height="12" rx="1" fill="none" stroke="var(--teal)" stroke-width="2"/><path d="M1 3 L9 9 L17 3" fill="none" stroke="var(--teal)" stroke-width="2"/></svg>
  <span>info@orbinfunding.example</span>
</div>
<div class="abs copyright">©ORBIN FUNDING GROUP - 2017. All Rights Reserved.</div>

</body>
</html>
```